Fenwick Ridge Accounting - New client package

I need a stationary package (presentation folder cover, welcome letter template/design, sample financial report template/design, business card and new logo) for my accounting business. I would like to see designs that use the color blue. Financial icons can be included in the design. The final design should be clean and communicate professionalism and the use of modern; user-friendly technology. Attached postcard files should help with overall design concept.

```html
<!DOCTYPE html>
<html lang="en">
<head>
<meta charset="utf-8">
<title>Fenwick Ridge Accounting – Business Card</title>
<link href="https://fonts.googleapis.com/css2?family=Roboto:wght@400;700&family=Saira+Condensed:wght@600&display=swap" rel="stylesheet">
<style>
  :root {
    --stage: #171717;
    --brand-blue: #2d5b8a;
    --brand-blue-soft: #3a6792;
    --paper: #f7f8f9;
    --ink: #3a3d40;
    --charcoal: #3c4044;
    --white: #ffffff;
  }
  * { margin: 0; padding: 0; box-sizing: border-box; }
  html, body { width: 1200px; height: 1200px; overflow: hidden; background: var(--stage); }
  body { position: relative; font-family: "Roboto", sans-serif; }

  .card {
    position: absolute;
    left: 318px;
    width: 562px;
    height: 339px;
    overflow: hidden;
  }
  .card--front { top: 251px; background: var(--brand-blue); }
  .card--back { top: 609px; background: var(--paper); }

  .front__disc {
    position: absolute;
    left: 110px; top: 0;
    width: 340px; height: 340px;
    border-radius: 50%;
    background: var(--brand-blue-soft);
  }
  .front__wordmark {
    position: absolute;
    left: 0; right: 0; top: 132px;
    text-align: center;
    color: var(--white);
    font-weight: 700;
    text-transform: uppercase;
  }
  .front__wordmark .name { display: block; font-size: 37px; letter-spacing: 2px; line-height: 1; }
  .front__wordmark .trade { display: block; font-size: 21px; letter-spacing: 15px; margin-top: 10px; padding-left: 15px; line-height: 1; }

  .back__mark {
    position: absolute;
    left: 86px; top: 46px;
    width: 126px; height: 126px;
    border-radius: 50%;
    background: var(--brand-blue);
  }
  .back__wordmark {
    position: absolute;
    left: 37px; width: 224px; top: 180px;
    text-align: center;
    color: var(--brand-blue);
    font-weight: 700;
    text-transform: uppercase;
    line-height: 1;
  }
  .back__wordmark .name { display: block; font-size: 20px; letter-spacing: 0.5px; }
  .back__wordmark .trade { display: block; font-size: 13px; letter-spacing: 8px; margin-top: 6px; padding-left: 8px; }

  .holder {
    position: absolute;
    right: 28px; top: 42px;
    text-align: right;
    color: var(--ink);
  }
  .holder__name { font-family: "Saira Condensed", sans-serif; font-weight: 600; font-size: 24px; color: var(--brand-blue); line-height: 1; }
  .holder__role { font-size: 14px; margin-top: 6px; }
  .holder__address { font-size: 14px; line-height: 21px; margin-top: 14px; font-style: normal; }

  .back__waves { position: absolute; left: 0; top: 0; }

  .contact {
    position: absolute;
    right: 22px; top: 252px;
    list-style: none;
    color: var(--white);
    font-size: 14.5px;
    line-height: 21px;
    text-align: right;
  }
  .contact li { display: flex; justify-content: flex-end; align-items: center; gap: 7px; }
  .contact svg { width: 12px; height: 12px; fill: var(--white); }
</style>
</head>
<body>

<section class="card card--front" aria-label="Business card front">
  <div class="front__disc"></div>
  <h1 class="front__wordmark">
    <span class="name">Fenwick Ridge</span>
    <span class="trade">Accounting</span>
  </h1>
</section>

<section class="card card--back" aria-label="Business card back">
  <svg class="back__waves" width="562" height="339" viewBox="0 0 562 339" aria-hidden="true">
    <path fill="var(--charcoal)" d="M0,250 C110,320 250,300 360,238 C440,192 500,178 562,182 L562,196 C500,188 440,204 362,248 C250,312 110,318 0,288 Z"/>
    <path fill="var(--brand-blue)" d="M0,298 C120,340 250,318 360,258 C440,214 500,200 562,208 L562,339 L0,339 Z"/>
    <path fill="var(--paper)" d="M40,270 C140,300 230,295 290,278 C220,300 130,300 40,270 Z"/>
  </svg>

  <div class="back__mark"></div>
  <div class="back__wordmark">
    <span class="name">Fenwick Ridge</span>
    <span class="trade">Accounting</span>
  </div>

  <div class="holder">
    <p class="holder__name">Marcus Hale</p>
    <p class="holder__role">Managing Director</p>
    <address class="holder__address">58 Harlow Lane,<br>Brookfield, US 40213</address>
  </div>

  <ul class="contact">
    <li>1.877.555.0142
      <svg viewBox="0 0 12 12" aria-hidden="true"><path d="M1,4 C1,2 3,1 6,1 C9,1 11,2 11,4 L9,4.5 L8.5,3.3 C7,2.9 5,2.9 3.5,3.3 L3,4.5 Z M2.5,11 L3.5,5.5 L8.5,5.5 L9.5,11 Z"/></svg>
    </li>
    <li>www.fenwickridgeaccounting.com
      <svg viewBox="0 0 12 12" aria-hidden="true"><circle cx="6" cy="6" r="5.2" fill="none" stroke="#fff" stroke-width="1"/><ellipse cx="6" cy="6" rx="2.2" ry="5.2" fill="none" stroke="#fff" stroke-width="1"/><path d="M1,6 H11" stroke="#fff" stroke-width="1"/></svg>
    </li>
    <li>info@fenwickridgeaccounting.com
      <svg viewBox="0 0 12 12" aria-hidden="true"><path d="M0.5,2.5 H11.5 V9.5 H0.5 Z M1.3,3.2 L6,6.8 L10.7,3.2" fill="none" stroke="#fff" stroke-width="1.2"/></svg>
    </li>
  </ul>
</section>

</body>
</html>
```